Our business name is Quillbrook Pty Ltd and we already have a logo. We would like the same colours that appear in our logo on our marketing material. I have attached our logo for colour consistency. We need a brochure designed that promotes our aerial photography and aerial imaging services. We'd like to use the brochure for electronic marketing purposes in an effort to attract a new client base. We are a new start up business so funds are fairly scarce. We use sophisticated UAV (unmanned aerial vehicle) or RPA - remotely piloted aircraft technology) that captures beautiful video and still images.
Our services are suitable for many types of industries and applications. We have identified at least 10 market sectors ranging, infrastructure inspections such as: gas pipelines, chemical and petrol storage facilities, pipeline and power line inspections, Archeological and geological surveys, vegetation mapping, wildlife surveys, agriculture and horticulture surveys, high end real estate, sport and event marketing. Our plan is to create a series of brochures (1) for each industry to help us market our business.

Our first brochure will focus on environmental management and compliance. We will target other industries down the track. These industries would see our service as helping them meet their compliance and auditing requirements.
We have a brochure that we put together containing words and some (very boring) format. As this will be one of a series of brochures, we'd like to colour code the industries for easy identification. (perhaps a green tab) in the corner to distinguish between our brochures. We have attached our boring brochure as a starting point. If we like the design there will be more work to follow. We want to be able to standardise the format for the other industries we will target. We anticipate needing another 6-8 brochures over the course of the next 2 months.

I have received questions regarding brochure size.  Apologies, I should have indicated in my posting previously.  The brochure is A3 landscape size so it can be folded in half to make 4 A4 pages.  We need to keep printing costs down so the content needs to be  within 4 pages.  I'm about to make some minor changes to the content to try to reduce the amount of text cause I can see this may be a problem.  Look forward to receiving your design. Thanking you in advance for your great work!

Re: Brochure Quillbrook Environmental Compliance and Monitoring Services

I have reduced the amount of text contained in the original version of the brochure making it more succinct and less wordy.  Could you use the least amount of space because we want to be able to use this brochure as both electric marketing and print based.  I have also included additional photos which will give you more to work with.  Thank you for your work in advance!  Regards Marta 

PLEASE NOTE - TEXT HAS BEEN UPDATED (REDUCED TEXT IN BROCHURE). COULD YOU REFER TO VERSION 2 OF QUILLBROOK ENVIRONMENTAL COMPLIANCE AND MONITORING SERVICES BROCHURE UPDATED FRIDAY 17TH.

Thanks Marta 

Hi talented designers working on the Quillbrook Brochure for Environmental Compliance and Monitoring.  I have been asked to upload the EPS version of Quillbrook Logo.  I have just done so.

Regards
Marta 

Hi all, to assist you with the design concept. I feel I need to clarity a number of points.  We are a new technology driven business.  No one else is conducting environmental surveys using this type of sophisticated equipment. We are in the business of providing clients with visual data (aerial images). Could you include grab lines in the brochure that draws attention to this. We us state of the art technology to produce high quality images efficiently, safely and economically. 

Thank you
Marta

Reason: We need additional time to receive and review designs.

Reason: Need additional time to communicate with designers and to review changes. Thank you Marta

I have extended the project date a few days. I have been incredibly impressed by the quality of your work and thank you all for your efforts.  I am waiting on a few revisions by a number of designers and look forward to receiving these changes.  We are close to completion.  Thanking you all again. Marta 

We are targeting a wide range of industry sectors. Specifically, looking at targeting large engineering type consultancies, corporations, government agencies, auditing bodies. Typically, targeting the professional sector who use data to confirm, monitor and make better decisions.

We want the brochure design to be contemporary and modern which reflects what our business does. We use state of the art unmanned aerial technology to capture brilliant visual images and video. So we want our brochure to reflect that we're leaders in the field offering something different - cutting edge approach. I have additional photos that show vegetation mapping, wildlife surveys, agriculture and horticulture applications. Our services would benefit any business that uses visual data to help them make better, more informed decisions.

Business

Serif
Sans Serif

• We would like you to include photo of the UAV equipment/technology shots. This is new technology so we must also educate our clients on what our technology is capable of doing. We are offering a service that is very different so we want to be able to convey the true benefits of our services such as safety, efficiency, cost saving, reliability. We would like to convey these key themes. Credible data enables businesses to make better, faster decisions.
• We are essentially providing visual data in the form of high definition photos and videos. For this particular sector, data could be used for compliance or auditing purposes, planning, measuring, monitoring, evaluating, assessing, marketing. Could you please include these words in the brochure as they capture our service provision. Please note the red photo is infrared images.

```html
<!DOCTYPE html>
<html lang="en">
<head>
<meta charset="utf-8">
<title>Quillbrook Brochure Spread</title>
<link href="https://fonts.googleapis.com/css2?family=Jost:wght@300;400;500&display=swap" rel="stylesheet">
<style>
  :root {
    --brand-blue: #29a9e0;
    --brand-blue-deep: #1b8fc4;
    --ink: #2e2e2e;
    --ink-dark: #1d1d1b;
    --paper: #ffffff;
    --paper-shade: #e6e6e6;
    --backdrop: #f2f2f2;
    --grass: #8bbf4a;
    --grass-light: #a9d36a;
    --tree: #4e6b2e;
  }
  html, body {
    margin: 0;
    padding: 0;
    width: 1200px;
    height: 886px;
    overflow: hidden;
    background: var(--backdrop);
    font-family: "Jost", "Futura", sans-serif;
  }
  .spread {
    position: absolute;
    left: 20px;
    top: 33px;
    width: 1160px;
    height: 819px;
    display: flex;
    box-shadow: 0 6px 18px rgba(0,0,0,0.18);
  }
  .page {
    position: relative;
    width: 580px;
    height: 819px;
    overflow: hidden;
    background: var(--paper);
  }
  .page--back { border-right: 1px solid #c9c9c9; }
  .page-art {
    position: absolute;
    inset: 0;
    width: 580px;
    height: 819px;
  }
  .profile {
    position: absolute;
    left: 43px;
    top: 225px;
    width: 488px;
    margin: 0;
    font-size: 14.6px;
    font-weight: 300;
    line-height: 20px;
    color: var(--ink);
    text-align: justify;
    text-indent: 50px;
    letter-spacing: 0.1px;
  }
  .wordmark {
    position: absolute;
    margin: 0;
    font-weight: 500;
    letter-spacing: -1px;
    line-height: 1;
  }
  .tagline {
    position: absolute;
    margin: 0;
    font-weight: 400;
    letter-spacing: 0.3px;
    line-height: 1;
  }
  .web {
    position: absolute;
    margin: 0;
    font-weight: 300;
    color: var(--paper);
    letter-spacing: 1px;
    line-height: 1;
  }
  .page--back .wordmark { left: 190px; top: 712px; font-size: 36px; color: var(--paper); }
  .page--back .tagline { left: 275px; top: 749px; font-size: 9px; color: var(--paper); }
  .page--back .web { left: 168px; top: 770px; font-size: 23px; }
  .page--front .wordmark { left: 256px; top: 562px; font-size: 46px; color: var(--ink-dark); }
  .page--front .tagline { left: 363px; top: 612px; font-size: 12px; color: var(--brand-blue); }
  .page--front .web { left: 282px; top: 727px; font-size: 23px; }
</style>
</head>
<body>
<main class="spread">
  <section class="page page--back">
    <svg class="page-art" viewBox="0 0 580 819" aria-hidden="true">
      <defs>
        <radialGradient id="paperShade" cx="0.35" cy="0.15" r="0.9">
          <stop offset="0" stop-color="#ffffff"/>
          <stop offset="0.6" stop-color="#f7f7f7"/>
          <stop offset="1" stop-color="#e4e4e4"/>
        </radialGradient>
      </defs>
      <rect width="580" height="819" fill="url(#paperShade)"/>
      <path d="M0,630 Q300,640 580,705" fill="none" stroke="var(--brand-blue)" stroke-width="2.5"/>
      <path d="M0,640 Q300,650 580,715 L580,819 L0,819 Z" fill="var(--brand-blue)"/>
    </svg>
    <p class="profile">Marta Velani is Quillbrook’s Business Development Manager. Marta has spent a considerable part of her career in the corporate sector where she worked for leading global companies such as Skyline Airways, Kestrel Motors and Norland Defence. She has held management roles in human resources, industrial relations and organisational development. Marta has a strong focus on project management /client relations, OH&amp;S, audits, compliance and quality management systems. She is one of few people in Australia to be accredited by Kestrel Motor Corporation (Japan) as a Total Quality Management Facilitator &amp; Assessor. Marta has spent a considerable part of her career supporting Engineering and Maintenance functions.</p>
    <p class="wordmark">QUILLBROOK</p>
    <p class="tagline">AERIAL &amp; SPATIAL IMAGING</p>
    <p class="web">www.quillbrook.com.au</p>
  </section>

  <section class="page page--front">
    <svg class="page-art" viewBox="0 0 580 819">
      <defs>
        <linearGradient id="parkTones" x1="0" y1="0" x2="1" y2="1">
          <stop offset="0" stop-color="var(--grass-light)"/>
          <stop offset="0.5" stop-color="var(--grass)"/>
          <stop offset="1" stop-color="var(--tree)"/>
        </linearGradient>
      </defs>
      <path role="img" aria-label="Aerial photograph of a green park with trees, a footpath and a red cycle path"
            d="M0,0 L580,0 L580,515 Q300,520 0,575 Z" fill="url(#parkTones)"/>
      <path d="M0,583 Q300,528 580,523" fill="none" stroke="var(--brand-blue-deep)" stroke-width="2"/>
      <path d="M0,697 Q300,640 580,630" fill="none" stroke="var(--brand-blue)" stroke-width="2.5"/>
      <path d="M0,707 Q300,650 580,640 L580,819 L0,819 Z" fill="var(--brand-blue)"/>
    </svg>
    <p class="wordmark">QUILLBROOK</p>
    <p class="tagline">AERIAL &amp; SPATIAL IMAGING</p>
    <p class="web">www.quillbrook.com.au</p>
  </section>
</main>
</body>
</html>
```